Brindle Children's Center - Child Care brochure

I just bought a new child care and completely renovated the space. We are also designing a new website, so I need the brochure to match that with updated info. www.brindlechildrenscenter.com - Information on there is current. We expect to have the new one up and running in the next few days. We have new photo's that I'd like to be added to the flyer too. ps. the boys in the pictures are mine, so i would appreciate one of them being added :). support@netcrafterhub.com has details on the website (dev.brindlechildrenscenter.com). The child care program is only open during the ski season - i.e. a resort facility catering to high end clients.
I'm attaching the the website information, the flyer I created, logo files and pictures.

Target Market(s)

Parents of young children

Font styles to use
Other font styles liked:
• "Things we said" & "Calibri Light"

Colors
cfeae6
fef1ee

Requirements
Must have
• Pictures of children. sleek design - winter, mountain theme. Check with website designer on new website.
Nice to have
• prices included
Should not have
• Kid like artwork

```html
<!DOCTYPE html>
<html lang="en">
<head>
<meta charset="utf-8">
<title>Brindle Children's Center – Brochure</title>
<link rel="stylesheet" href="https://fonts.googleapis.com/css2?family=Open+Sans:wght@300;400&display=swap">
<style>
  :root{
    --stage:#e6e4e2;
    --blush:#fef1ee;
    --blush-deep:#f9e3df;
    --mint:#6fc59a;
    --ink:#3a3a3a;
    --rule:#b9c9c0;
    --white:#ffffff;
    --sky:#b9cfe6;
    --snow:#f3f5f8;
    --pine:#5d6b5f;
  }
  *{margin:0;padding:0;box-sizing:border-box}
  html,body{width:1200px;height:923px;overflow:hidden}
  body{background:var(--stage);font-family:"Open Sans",Arial,sans-serif;color:var(--ink);position:relative}
  .brochure{position:absolute;left:86px;top:65px;width:1029px;height:795px;display:flex;box-shadow:0 4px 14px rgba(0,0,0,.18);background:var(--white)}
  .panel{position:relative;width:343px;height:100%;overflow:hidden}
  .panel + .panel{border-left:1px dashed #c9bdb9}

  .section-band{position:absolute;left:18px;width:300px;height:20px;background:var(--mint);color:var(--white);font-size:14px;font-weight:400;line-height:20px;padding-left:8px}
  .body-copy{position:absolute;left:18px;width:300px;font-size:11px;line-height:14.5px;color:var(--ink)}

  /* reservations panel */
  .panel--reservations{background:linear-gradient(90deg,var(--blush) 0%,var(--blush-deep) 100%)}
  .name-disc{position:absolute;border-radius:50%;background:var(--white);display:flex;align-items:center;justify-content:center;text-align:center;color:var(--ink);font-weight:400}
  .form-title{position:absolute;left:22px;top:311px;font-size:16px;font-weight:400}
  .form-label{position:absolute;left:22px;font-size:11px;color:var(--ink)}
  .form-line{position:absolute;left:22px;width:296px;border-bottom:1px dashed var(--rule)}

  /* contact panel */
  .photo{position:absolute}
  .photo--slopes-left{left:0;top:0;width:343px;height:380px;background:linear-gradient(180deg,var(--sky) 0%,#dfe7ef 30%,var(--pine) 52%,#e9edf1 68%,var(--white) 100%)}
  .photo--children{left:0;top:596px;width:343px;height:199px;background:linear-gradient(135deg,#d7d3d0 0%,#c8b9b7 45%,#4c6470 75%,#d8d2cc 100%)}
  .address{position:absolute;left:120px;font-size:10px;line-height:14px;white-space:nowrap}

  /* cover panel */
  .photo--slopes-right{left:0;top:0;width:343px;height:545px;background:linear-gradient(180deg,var(--sky) 0%,#e4ebf2 28%,#8f8478 48%,#eef1f4 62%,var(--snow) 100%)}
  .welcome-band{position:absolute;left:0;top:545px;width:343px;height:91px;background:var(--mint);color:var(--white);font-size:25px;font-weight:300;line-height:32px;text-align:center;padding-top:14px}
  .mission{position:absolute;left:0;top:636px;width:343px;height:159px;background:var(--blush);padding:14px 16px 0 22px;font-size:17.5px;line-height:24px;color:#222}
</style>
</head>
<body>
<main class="brochure">

  <section class="panel panel--reservations">
    <div class="section-band" style="top:30px">Reservations</div>
    <p class="body-copy" style="top:55px">We highly recommend that reservations be made in advance to ensure space for your child.<br>To make a reservation contact us at: 555-014-2290.<br>We have limited capacity.</p>

    <div class="name-disc" style="left:90px;top:143px;width:148px;height:148px;font-size:14px;line-height:18px">Brindle<br>Children's<br>Center</div>

    <h2 class="form-title">Reservation Conformation:</h2>
    <span class="form-label" style="top:343px">Conformation Number:</span>
    <div class="form-line" style="top:376px"></div>

    <span class="form-label" style="top:389px">Child's Name:</span>
    <span class="form-label" style="top:413px">1)</span>
    <div class="form-line" style="top:428px;left:36px;width:150px"></div>
    <span class="form-label" style="top:413px;left:210px">Age:</span>
    <div class="form-line" style="top:428px;left:240px;width:78px"></div>
    <span class="form-label" style="top:436px">2)</span>
    <div class="form-line" style="top:451px;left:36px;width:150px"></div>
    <span class="form-label" style="top:436px;left:210px">Age:</span>
    <div class="form-line" style="top:451px;left:240px;width:78px"></div>
    <span class="form-label" style="top:459px">3)</span>
    <div class="form-line" style="top:474px;left:36px;width:150px"></div>
    <span class="form-label" style="top:459px;left:210px">Age:</span>
    <div class="form-line" style="top:474px;left:240px;width:78px"></div>

    <span class="form-label" style="top:506px">Reserved Dates:</span>
    <div class="form-line" style="top:545px"></div>
    <span class="form-label" style="top:553px">Reservation Fee:</span>
    <div class="form-line" style="top:595px"></div>

    <p class="body-copy" style="top:616px;left:22px">Your reservation fee will be applied to your last day of service.</p>

    <div class="section-band" style="top:695px">Cancellation Policy</div>
    <p class="body-copy" style="top:719px">Reservations must be cancelled 24hrs in advance of the date(s) of service or full fee will be charged for all days not cancelled.</p>
  </section>

  <section class="panel panel--contact">
    <div class="photo photo--slopes-left" role="img" aria-label="Snowy mountain slopes with pine trees and the ski lodge buildings"></div>

    <div class="section-band" style="top:374px;left:22px">Contact Us :</div>
    <p class="body-copy" style="top:399px;left:22px">The Brindle Childrens Center is located in the Juniper Basin Base at the Brindle Ski Resort in Utah. It is on the third floor of the Halvorsen Ski School Building.</p>

    <div class="name-disc" style="left:20px;top:472px;width:90px;height:90px;font-size:10px;line-height:13px">Brindle<br>Children's<br>Center</div>

    <p class="address" style="top:468px">Brindle Children's Center<br>4180 Pinecrest Lodge Road<br>Brindle, UT 84000</p>
    <p class="address" style="top:526px">Telephone: +1 555 014-2290</p>
    <p class="address" style="top:547px">Email: fun@brindlechildrenscenter.com</p>
    <p class="address" style="top:568px">Website: dev.brindlechildrenscenter.com</p>

    <div class="photo photo--children" role="img" aria-label="Two young children sitting together reading a picture book"></div>
  </section>

  <section class="panel panel--cover">
    <div class="photo photo--slopes-right" role="img" aria-label="Ski base area with the lodge building and skiers on the snow"></div>

    <div class="name-disc" style="left:53px;top:276px;width:228px;height:228px;font-size:22px;line-height:28px">Brindle<br>Children's<br>Center</div>

    <h1 class="welcome-band">Welcome to the<br>Brindle Children's Center!</h1>
    <p class="mission">Our mission is to ensure that all children from across the globe feel safe, have fun and create magical vacation memories!</p>
  </section>

</main>
</body>
</html>
```